Business Card Design needed - Something Awesome!

Need a business card designed. Company is "Marlowe Advisory" we do consulting and also have sales automation technology.
I'm going to use thick stock or metal, something really nice... I was thinking about a QR Code on the back that would just upload my contact info to the persons contact, etc -

This is a Strategy Company with a tech feel. I'm open to ideas but really want this to be nice!

I need a template that should include:

Name | Position or Title
D: 415.902.3376
www.marloweadvisory.example

I'm going to attach my contact so you can use that one, I need to get this printed.

Target Market(s)

Small to mid size customers, Entrepreneurs etc.

Industry/Entity Type

Consulting, Tech, Private Equity.

Contact Information for Business Card

Name, Phone, Maybe email, URL

Font styles to use
Sans Serif

Colors

Designer to choose only greyscale colors for use in the design.

Requirements
Must have
• Fresh, Clean, stand out from the crowd - will be on thick stock or metal.
Nice to have
• Clean, simple yet impactful.
Should not have
• Not cartoonish

```html
<!DOCTYPE html>
<html lang="en">
<head>
<meta charset="utf-8">
<title>Marlowe Advisory — Business Card</title>
<link href="https://fonts.googleapis.com/css2?family=Lato:wght@300;400;700&display=swap" rel="stylesheet">
<style>
  :root {
    --backdrop: #262626;
    --card: #121212;
    --card-edge: #1b1b1b;
    --emboss: #171717;
    --ink-bright: #e6e6e6;
    --ink-mid: #b3b3b3;
    --ink-soft: #7a7a7a;
  }
  * { margin: 0; padding: 0; box-sizing: border-box; }
  html, body {
    width: 1200px;
    height: 1039px;
    overflow: hidden;
    background: var(--backdrop);
    font-family: "Lato", sans-serif;
  }
  .canvas {
    position: relative;
    width: 1200px;
    height: 1039px;
  }
  .card {
    position: absolute;
    width: 560px;
    height: 320px;
    background: var(--card);
    border: 1px solid var(--card-edge);
    box-shadow: 0 24px 50px rgba(0,0,0,0.45);
    overflow: hidden;
  }
  .card--front { left: 70px; top: 150px; }
  .card--back { left: 570px; top: 570px; }

  .emboss-field {
    position: absolute;
    background: var(--emboss);
  }
  .card--front .emboss-field { right: 0; top: 0; width: 230px; height: 320px; }
  .card--back .emboss-field { left: 0; bottom: 0; width: 300px; height: 200px; }

  .wordmark {
    position: absolute;
    left: 70px;
    top: 132px;
    display: flex;
    align-items: center;
    gap: 14px;
    color: var(--ink-bright);
    font-weight: 400;
    font-size: 44px;
    letter-spacing: 5px;
  }
  .wordmark__square {
    width: 14px;
    height: 14px;
    background: var(--ink-bright);
  }

  .contact {
    position: absolute;
    right: 34px;
    top: 34px;
    text-align: right;
  }
  .contact__name {
    color: var(--ink-bright);
    font-weight: 700;
    font-size: 24px;
    letter-spacing: 0.3px;
  }
  .contact__title {
    color: var(--ink-soft);
    font-weight: 300;
    font-size: 16px;
    margin-top: 2px;
    margin-bottom: 16px;
  }
  .contact__line {
    display: flex;
    justify-content: flex-end;
    align-items: center;
    gap: 10px;
    color: var(--ink-mid);
    font-weight: 300;
    font-size: 14px;
    line-height: 22px;
  }
  .contact__icon { width: 12px; height: 12px; flex: none; }
</style>
</head>
<body>
<main class="canvas">

  <section class="card card--front" aria-label="Card front">
    <div class="emboss-field" role="img" aria-label="Blind-embossed geometric brand pattern"></div>
    <div class="wordmark">
      <span class="wordmark__square"></span>
      <span class="wordmark__name">MARLOWE</span>
    </div>
  </section>

  <section class="card card--back" aria-label="Card back">
    <div class="emboss-field" role="img" aria-label="Blind-embossed geometric brand pattern"></div>
    <div class="contact">
      <div class="contact__name">Adrian K.Holloway</div>
      <div class="contact__title">Founder/CEO</div>
      <div class="contact__line">
        <span>415.902.3376</span>
        <svg class="contact__icon" viewBox="0 0 12 12" aria-hidden="true">
          <path d="M2.5 1h2l1 2.5-1.3 1a6 6 0 0 0 3.3 3.3l1-1.3L11 7.5v2a1 1 0 0 1-1 1A9 9 0 0 1 1.5 2a1 1 0 0 1 1-1z" fill="#b3b3b3"/>
        </svg>
      </div>
      <div class="contact__line">
        <span>hello@marloweadvisory.example</span>
        <svg class="contact__icon" viewBox="0 0 12 12" aria-hidden="true">
          <rect x="0.5" y="2.5" width="11" height="7" fill="#b3b3b3"/>
          <path d="M0.5 2.5 6 6.5l5.5-4" fill="none" stroke="#121212" stroke-width="1"/>
        </svg>
      </div>
      <div class="contact__line">
        <span>marloweadvisory.example</span>
        <svg class="contact__icon" viewBox="0 0 12 12" aria-hidden="true">
          <circle cx="6" cy="6" r="5.2" fill="none" stroke="#b3b3b3" stroke-width="1.2"/>
          <path d="M0.8 6h10.4M6 0.8c-2.5 2.8-2.5 7.6 0 10.4M6 0.8c2.5 2.8 2.5 7.6 0 10.4" fill="none" stroke="#b3b3b3" stroke-width="0.9"/>
        </svg>
      </div>
    </div>
  </section>

</main>
</body>
</html>
```